Design and Renovation Company Luxury Business Card

I want to create a luxury business card for a Design and Renovation Firm . We will use our current logo. The company name is 528BUILDA. We do not want anything standard. We need a very unique concept.
Please see uploaded inspiration. I really like the textured paper option. I would like the card to be thick with debossing, and/or embossing options. The logo has orange in it but I would like to see the card with and without the orange. I think the orange may make the company feel less high-end. The goal is to elevate the logo not match its vibe per se of the logo. We want something very unique, not standard at all!
I would like a space for :
Logo,
Name,
Position,
Email,
Office number,
Website Address,
Business Address,
Thank you!
Have fun!
Target Market(s)
Home owners Age 35 +
Industry/Entity Type
Design and Renovation
Contact Information for Business Card
Logo, Name, Position, Email, Office number, Website Address, Business Address,.
Colors
Designer to choose colors to be used in the design.
Requirements
Must have
- A luxury designer feel. Must be black or dark grey but open to other luxury ideas.
Nice to have
- Gold, silver, black embossing or debossing. Textured paper design.
Should not have
- A cheap look and feel.

```html
<!DOCTYPE html>
<html lang="en">
<head>
<meta charset="utf-8">
<title>528BUILDA Business Card</title>
<link rel="stylesheet" href="https://fonts.googleapis.com/css2?family=Montserrat:wght@400;500;600;700&display=swap">
<style>
  :root {
    --backdrop: #9b9b9b;
    --paper-white: #f6f6f4;
    --paper-black: #1e1e1e;
    --ink-dark: #222222;
    --ink-light: #f2f2f2;
    --accent-orange: #e8901c;
    --edge-orange: #d9800f;
  }
  * { box-sizing: border-box; margin: 0; padding: 0; }
  html, body {
    width: 1200px;
    height: 956px;
    overflow: hidden;
    background: var(--backdrop);
    font-family: "Montserrat", sans-serif;
  }
  .canvas {
    position: relative;
    width: 1200px;
    height: 956px;
  }
  .card {
    position: absolute;
    width: 560px;
    height: 320px;
    border-radius: 3px;
    box-shadow: 0 4px 0 var(--edge-orange), 0 18px 36px rgba(0,0,0,0.28);
  }
  .card--front {
    left: 110px;
    top: 110px;
    background:
      radial-gradient(circle at 70% 40%, rgba(255,255,255,0.7), rgba(235,235,232,0.4) 70%),
      var(--paper-white);
    color: var(--ink-dark);
    padding: 44px 0 0 46px;
  }
  .card--back {
    left: 530px;
    top: 520px;
    background:
      radial-gradient(circle at 35% 30%, rgba(60,60,60,0.35), rgba(0,0,0,0) 70%),
      var(--paper-black);
    color: var(--ink-light);
    display: flex;
    flex-direction: column;
    justify-content: center;
    padding-left: 70px;
  }

  .brand {
    display: flex;
    align-items: center;
    gap: 12px;
  }
  .brand__square {
    width: 22px;
    height: 22px;
    background: var(--accent-orange);
  }
  .brand__name {
    font-weight: 600;
    font-size: 34px;
    letter-spacing: 2px;
    line-height: 1;
  }
  .brand__tagline {
    font-weight: 500;
    font-size: 9px;
    letter-spacing: 3.6px;
    margin: 6px 0 0 34px;
  }

  .card--back .brand__square { width: 44px; height: 44px; }
  .card--back .brand__name { font-size: 64px; letter-spacing: 4px; color: var(--ink-light); }
  .card--back .brand__tagline { font-size: 15px; letter-spacing: 6px; margin: 10px 0 0 58px; font-weight: 600; }

  .holder { margin-top: 26px; }
  .holder__name {
    color: var(--accent-orange);
    font-weight: 700;
    font-size: 20px;
    letter-spacing: 0.5px;
  }
  .holder__role {
    font-size: 12px;
    margin-top: 2px;
  }
  .address {
    font-size: 12px;
    line-height: 1.45;
    margin-top: 12px;
  }
  .contact {
    list-style: none;
    margin-top: 12px;
    font-size: 12px;
    line-height: 1.7;
  }
  .contact__item {
    display: flex;
    align-items: center;
    gap: 9px;
  }
  .contact__icon {
    width: 11px;
    height: 11px;
    flex: none;
  }
</style>
</head>
<body>
<main class="canvas">

  <section class="card card--front" aria-label="Card front">
    <div class="brand">
      <span class="brand__square"></span>
      <span class="brand__name">528BUILDA</span>
    </div>
    <p class="brand__tagline">Design and Renovation Firm</p>

    <div class="holder">
      <p class="holder__name">DANA WHITLOW</p>
      <p class="holder__role">Medical Director</p>
    </div>

    <p class="address">412 Harbor Crest Lane Suite 18<br>Ashford, New York 11920</p>

    <ul class="contact">
      <li class="contact__item">
        <svg class="contact__icon" viewBox="0 0 12 12" aria-hidden="true"><path fill="var(--accent-orange)" d="M2.5 0.8l2 2.1-1 1.3c.7 1.5 1.8 2.6 3.3 3.3l1.3-1 2.1 2-1.2 2.1C5 10.5 1.5 7 .9 2z"/></svg>
        <span>(000)555-0192</span>
      </li>
      <li class="contact__item">
        <svg class="contact__icon" viewBox="0 0 12 12" aria-hidden="true"><rect x="0.5" y="2" width="11" height="8" fill="var(--accent-orange)"/><path d="M1 2.6l5 3.8 5-3.8" stroke="#fff" stroke-width="1" fill="none"/></svg>
        <span>info@528builda.com</span>
      </li>
      <li class="contact__item">
        <svg class="contact__icon" viewBox="0 0 12 12" aria-hidden="true"><circle cx="6" cy="6" r="5.5" fill="var(--accent-orange)"/><path d="M0.5 6h11M6 0.5c-2.5 3-2.5 8 0 11M6 0.5c2.5 3 2.5 8 0 11" stroke="#fff" stroke-width="0.8" fill="none"/></svg>
        <span>www.528builda.com</span>
      </li>
    </ul>
  </section>

  <section class="card card--back" aria-label="Card back">
    <div class="brand">
      <span class="brand__square"></span>
      <span class="brand__name">528BUILDA</span>
    </div>
    <p class="brand__tagline">Design and Renovation Firm</p>
  </section>

</main>
</body>
</html>
```